QVR business card

Need a business card for a company that provides instructional design and elearning development services. The website is here: http://quorvane.studio/

I'm attaching a current logo, as well as the old business card design. While I like to keep it clean, the old design is too simplistic for my liking. The only idea I want to reuse from the old design is placing industry jargon on the back of the card, just need a better way to present it. But if you have other ideas for the back--feel free to experiment.

Please use the colors complementary to the color we have on the website. Thank you!

```html
<!DOCTYPE html>
<html lang="en">
<head>
<meta charset="utf-8">
<title>QVR business card</title>
<link rel="stylesheet" href="https://fonts.googleapis.com/css2?family=Open+Sans:wght@400;600;700&display=swap">
<style>
  :root {
    --backdrop: #ecebe8;
    --kraft-light: #d2b589;
    --kraft: #c6a678;
    --kraft-dark: #b8966a;
    --ink: #161310;
    --shadow: rgba(60, 40, 20, 0.22);
  }
  * { box-sizing: border-box; margin: 0; padding: 0; }
  html, body {
    width: 1200px; height: 900px; overflow: hidden;
    background: var(--backdrop);
    font-family: "Open Sans", Arial, sans-serif;
    color: var(--ink);
  }
  .canvas { position: relative; width: 1200px; height: 900px; }
  .card {
    position: absolute;
    background: linear-gradient(135deg, var(--kraft-light) 0%, var(--kraft) 55%, var(--kraft-dark) 100%);
    box-shadow: 0 6px 18px var(--shadow);
  }
  .card-front { left: 238px; top: 62px; width: 555px; height: 342px; }
  .card-back { left: 458px; top: 518px; width: 559px; height: 342px; }

  .brand {
    position: absolute; left: 0; right: 0; top: 72px;
    display: flex; align-items: center; justify-content: center; gap: 14px;
  }
  .brand-square { width: 40px; height: 40px; background: var(--ink); }
  .brand-name { font-weight: 700; font-size: 64px; line-height: 1; letter-spacing: 2px; }

  .holder-name {
    position: absolute; left: 46px; top: 232px;
    font-weight: 700; font-size: 17px;
  }
  .contact-list { position: absolute; left: 252px; top: 216px; list-style: none; }
  .contact-item {
    display: flex; align-items: center; gap: 8px;
    height: 20px; font-size: 14px;
  }
  .contact-icon { width: 12px; height: 12px; fill: var(--ink); flex: none; }

  .help-title {
    position: absolute; left: 36px; top: 68px;
    font-weight: 600; font-size: 22px; letter-spacing: 0.2px;
  }
  .service-list { position: absolute; left: 40px; top: 113px; list-style: none; }
  .service-item {
    position: relative; padding-left: 15px;
    height: 27px; line-height: 27px; font-size: 19.5px;
  }
  .service-item::before {
    content: ""; position: absolute; left: 0; top: 11px;
    width: 7px; height: 7px; border-radius: 50%; background: var(--ink);
  }
  .back-brand {
    position: absolute; left: 322px; top: 132px;
    display: flex; align-items: center; gap: 12px;
  }
  .back-brand-circle { width: 34px; height: 34px; border-radius: 50%; background: var(--ink); }
  .back-brand-name { font-weight: 700; font-size: 64px; line-height: 1; letter-spacing: 2px; }
</style>
</head>
<body>
<main class="canvas">
  <section class="card card-front">
    <div class="brand">
      <span class="brand-square"></span>
      <span class="brand-name">QVR</span>
    </div>
    <p class="holder-name">Marten Loraux</p>
    <ul class="contact-list">
      <li class="contact-item">
        <svg class="contact-icon" viewBox="0 0 12 12"><path d="M2.4 0.6 4.2 2.6 3.2 4.1C3.9 5.6 5.2 7 6.9 7.9L8.4 6.9 10.9 8.6 9.8 11C5 10.6 1.2 6.8 0.8 1.9Z"/></svg>
        <span>555-014-2287</span>
      </li>
      <li class="contact-item">
        <svg class="contact-icon" viewBox="0 0 12 12"><path d="M1 3h10v6.5H1Z M1 3l5 3.6L11 3" fill="var(--ink)" stroke="var(--kraft)" stroke-width="0.8"/></svg>
        <span>mloraux@quorvane.studio</span>
      </li>
      <li class="contact-item">
        <svg class="contact-icon" viewBox="0 0 12 12"><circle cx="6" cy="6" r="5"/><path d="M4 3.5c1 .3 1.5 1 1 1.8-.5.8.2 1.4 1 1.4s.9 1.2.3 2.3M7.5 2c-.3.8.3 1.4 1.3 1.5" stroke="var(--kraft)" stroke-width="0.9" fill="none"/></svg>
        <span>www.quorvane.studio</span>
      </li>
    </ul>
  </section>

  <section class="card card-back">
    <h2 class="help-title">HOW CAN WE HELP?</h2>
    <ul class="service-list">
      <li class="service-item">Mobile Learning Scorm</li>
      <li class="service-item">Instructional Design Lms</li>
      <li class="service-item">Moocs Elearning Html5</li>
      <li class="service-item">Adult Learning Theory</li>
      <li class="service-item">Gamification Classroom</li>
      <li class="service-item">Xapi Blended Learning</li>
    </ul>
    <div class="back-brand">
      <span class="back-brand-circle"></span>
      <span class="back-brand-name">QVR</span>
    </div>
  </section>
</main>
</body>
</html>
```